Thornbury Building Company - Card Design

I am looking to use the logo designs that you already did for me to develop a business card. I would like the card to have a black background and be double sided. I want white and green logo and text. I have attached an inspiration photo of a look that I like. I would like to use the Vertical Logo attached to take up the full front side of the card. On the back where I have my name and information, I would like to have the horizontal logo or maybe even just the image of the 'A' and trees without the text. I am open, but I am looking for something clean and simple and I want the green to really pop! Additional files can be found under Design #: 58302946

Target Market(s)

Homeowners

Industry/Entity Type

Construction

Contact Information for Business Card

Name: Marcus Thornbury, Title: Project Manager, Phone: 555.274.8136, Email: thornburybuildingcompany@mailvesta.com, address: 487 Larkspur Ln, Ashgrove, OR 95033, Lic# 2468317

Colors
00AB8E
00BBA5
67D7C9
C6EFE9
E9F9F6

Requirements
Nice to have
• I would like to see the logos that I have already got from ArtLoomHub, though I am open to new ones

```html
<!DOCTYPE html>
<html lang="en">
<head>
<meta charset="utf-8">
<title>Thornbury Building Company – Business Card</title>
<link href="https://fonts.googleapis.com/css2?family=Open+Sans:wght@400;600;700&display=swap" rel="stylesheet">
<style>
  :root {
    --backdrop: #4a4a4a;
    --card: #151515;
    --green: #4cb848;
    --green-bright: #5cc34f;
    --white: #ffffff;
  }
  * { box-sizing: border-box; margin: 0; padding: 0; }
  html, body {
    width: 1200px;
    height: 801px;
    overflow: hidden;
    background: var(--backdrop);
    font-family: "Open Sans", Arial, sans-serif;
  }
  .stage {
    width: 1200px;
    height: 801px;
    display: flex;
    align-items: center;
    justify-content: center;
    gap: 50px;
  }
  .card {
    width: 525px;
    height: 300px;
    background: var(--card);
    border-bottom: 3px solid var(--green);
    position: relative;
    box-shadow: 0 12px 30px rgba(0,0,0,0.45);
    overflow: hidden;
  }

  /* Back side: contact details */
  .card-back { display: flex; align-items: center; padding: 0 20px; }
  .back-brand {
    width: 175px;
    flex: none;
    display: flex;
    align-items: center;
    gap: 9px;
  }
  .brand-mark {
    width: 18px;
    height: 18px;
    border-radius: 50%;
    background: var(--green);
    flex: none;
  }
  .brand-name {
    color: var(--white);
    font-weight: 700;
    font-size: 15px;
    line-height: 1.25;
    letter-spacing: 0.3px;
  }
  .divider {
    width: 1px;
    height: 150px;
    background: var(--green);
    margin: 0 16px 0 8px;
    flex: none;
  }
  .contact { color: var(--white); min-width: 0; }
  .contact-name {
    color: var(--green-bright);
    font-weight: 700;
    font-size: 20px;
    line-height: 1.15;
  }
  .contact-title {
    font-size: 13.5px;
    margin-bottom: 12px;
  }
  .contact-list { list-style: none; font-size: 11px; line-height: 1.7; }
  .contact-list li { display: flex; align-items: center; gap: 6px; white-space: nowrap; }
  .contact-list svg { width: 10px; height: 10px; fill: var(--green); flex: none; }
  .license { font-size: 12px; margin-top: 10px; }

  /* Front side: brand */
  .card-front { display: flex; align-items: center; justify-content: center; }
  .front-ring {
    width: 230px;
    height: 230px;
    border: 5px solid var(--white);
    border-radius: 50%;
    display: flex;
    align-items: center;
    justify-content: center;
    text-align: center;
  }
  .front-name {
    color: var(--white);
    font-weight: 700;
    font-size: 24px;
    line-height: 1.25;
    letter-spacing: 1px;
  }
</style>
</head>
<body>
<main class="stage">
  <section class="card card-back" aria-label="Business card back">
    <div class="back-brand">
      <span class="brand-mark"></span>
      <span class="brand-name">Thornbury Building Company</span>
    </div>
    <div class="divider"></div>
    <div class="contact">
      <div class="contact-name">Marcus Thornbury</div>
      <div class="contact-title">Project Manager</div>
      <ul class="contact-list">
        <li>
          <svg viewBox="0 0 24 24"><path d="M6.6 10.8a15 15 0 0 0 6.6 6.6l2.2-2.2a1 1 0 0 1 1-.25 11.4 11.4 0 0 0 3.6.57 1 1 0 0 1 1 1V20a1 1 0 0 1-1 1A17 17 0 0 1 3 4a1 1 0 0 1 1-1h3.5a1 1 0 0 1 1 1c0 1.25.2 2.45.57 3.57a1 1 0 0 1-.25 1z"/></svg>
          555.274.8136
        </li>
        <li>
          <svg viewBox="0 0 24 24"><path d="M2 5h20v14H2z M2 5l10 8 10-8"/></svg>
          thornburybuildingcompany@mailvesta.com
        </li>
        <li>
          <svg viewBox="0 0 24 24"><path d="M12 2a7 7 0 0 0-7 7c0 5 7 13 7 13s7-8 7-13a7 7 0 0 0-7-7zm0 9.5A2.5 2.5 0 1 1 12 6.5a2.5 2.5 0 0 1 0 5z"/></svg>
          487 Larkspur Ln, Ashgrove, OR 95033
        </li>
      </ul>
      <div class="license">License# 2468317</div>
    </div>
  </section>

  <section class="card card-front" aria-label="Business card front">
    <div class="front-ring">
      <span class="front-name">Thornbury<br>Building<br>Company</span>
    </div>
  </section>
</main>
</body>
</html>
```